Mindfulness School for Children -- Business Cards

We're looking for business cards for our school directors and owners. We're a mindfulness school for children called little lanterns. Attached are our logos/icons.

```html
<!DOCTYPE html>
<html lang="en">
<head>
<meta charset="utf-8">
<title>little lanterns — Business Cards</title>
<link rel="stylesheet" href="https://fonts.googleapis.com/css2?family=Lora:wght@400;500&family=Karla:wght@400;500&display=swap">
<style>
  :root {
    --stage: #e9ebec;
    --card-dark: #242424;
    --card-light: #fbfbfa;
    --teal: #55afc6;
    --teal-soft: #7cc2d3;
    --sea-green: #6cb39b;
    --white: #ffffff;
    --brand-text: #62b7cc;
  }
  * { margin: 0; padding: 0; box-sizing: border-box; }
  html, body {
    width: 1200px; height: 874px; overflow: hidden;
    background: var(--stage);
  }
  .sheet {
    width: 1200px; height: 874px;
    display: flex; flex-direction: column;
    align-items: center; justify-content: center; gap: 40px;
  }
  .card {
    position: relative;
    width: 640px; height: 366px;
    border-radius: 22px;
    overflow: hidden;
    box-shadow: 0 6px 18px rgba(0,0,0,0.12);
  }
  /* Back side */
  .card--back {
    background: var(--card-dark);
    display: flex; align-items: center; justify-content: center;
  }
  .brand-name {
    font-family: "Lora", serif;
    font-weight: 400;
    font-size: 62px;
    letter-spacing: 0.5px;
    color: var(--brand-text);
  }
  /* Front side */
  .card--front { background: var(--card-light); }
  .card__art { position: absolute; inset: 0; }
  .contact {
    position: absolute; left: 46px; top: 46px;
    color: var(--white);
    font-family: "Karla", sans-serif;
  }
  .contact__name {
    font-family: "Lora", serif;
    font-weight: 400;
    font-size: 31px;
    line-height: 1.1;
  }
  .contact__role {
    font-size: 15px;
    margin-bottom: 14px;
    letter-spacing: 0.3px;
  }
  .contact__list { list-style: none; font-size: 15px; line-height: 1.35; }
  .contact__item { display: flex; align-items: flex-start; gap: 9px; margin-bottom: 3px; }
  .contact__icon { width: 13px; height: 13px; flex: none; margin-top: 3px; }
</style>
</head>
<body>
<main class="sheet">
  <section class="card card--back" aria-label="Card back">
    <span class="brand-name">little lanterns</span>
  </section>

  <section class="card card--front" aria-label="Card front">
    <svg class="card__art" width="640" height="366" viewBox="0 0 640 366" aria-hidden="true">
      <path d="M0 0 H470 C440 190 330 318 150 326 C90 328 40 316 0 296 Z" fill="var(--teal)"/>
      <path d="M0 300 C60 332 200 346 330 334 C210 356 80 350 0 316 Z" fill="var(--sea-green)"/>
      <circle cx="508" cy="262" r="66" fill="var(--teal-soft)" opacity="0.35"/>
    </svg>

    <div class="contact">
      <h1 class="contact__name">Daniel Reyes</h1>
      <p class="contact__role">President</p>
      <ul class="contact__list">
        <li class="contact__item">
          <svg class="contact__icon" viewBox="0 0 12 12"><path d="M6 0.5a4 4 0 0 0-4 4c0 3 4 7 4 7s4-4 4-7a4 4 0 0 0-4-4zm0 5.5a1.5 1.5 0 1 1 0-3 1.5 1.5 0 0 1 0 3z" fill="currentColor"/></svg>
          <span>2140 Willow Bend Road<br>Juneau, Alaska 34518</span>
        </li>
        <li class="contact__item">
          <svg class="contact__icon" viewBox="0 0 12 12"><path d="M2.5 0.8l2 2-1 1.4c.7 1.5 1.8 2.6 3.3 3.3l1.4-1 2 2-1.3 1.8C5 10 1.9 6.9 0.7 2.1z" fill="currentColor"/></svg>
          <span>369-482-1730</span>
        </li>
        <li class="contact__item">
          <svg class="contact__icon" viewBox="0 0 12 12"><rect x="0.5" y="2" width="11" height="8" rx="1" fill="currentColor"/><path d="M1 2.6l5 3.8 5-3.8" fill="none" stroke="var(--teal)" stroke-width="1"/></svg>
          <span>name@littlelanterns.com</span>
        </li>
        <li class="contact__item">
          <svg class="contact__icon" viewBox="0 0 12 12"><circle cx="6" cy="6" r="5.5" fill="currentColor"/><path d="M0.8 6h10.4M6 0.5c-2 2.8-2 8.2 0 11M6 0.5c2 2.8 2 8.2 0 11" fill="none" stroke="var(--teal)" stroke-width="0.8"/></svg>
          <span>littlelanterns.com</span>
        </li>
      </ul>
    </div>
  </section>
</main>
</body>
</html>
```